Flyer Vacation Gift Certificate

I need to create a beautiful flyer 8.5 x 11 PDF format flyer design. <br/><br/>Instructions:<br/>The flyer will really be a gift voucher for a las vegas vacation getaway. So must have a Las Vegas Theme exciting fun<br/><br/>The voucher should have two modules that will be editable. <br/>Must have a "Compliments Of" area and also must have an "Exclusively For" area<br/><br/>Keep in mind that this flyer will be printed so keep that in mind :)<br/><br/>Here the is the content for the vacation voucher:<br/><br/>There is no doubt that Las Vegas is one of the hottest travel destinations around the world. In fact, some people would even go as far as<br/>saying that perhaps it is THE hottest place to visit. Enjoy up to 4 nights of resort/casino accommodations in exciting Las Vegas, NV. Millions of people travel to this exciting city each year to enjoy its thrills. Thanks to the business you received this certificate from, now you can enjoy exciting Las Vegas, NV too!<br/><br/>Features:<br/>*Travel 7 Days A Week<br/>*Stay Your Choice Of Nights (1-4 Nights)<br/>*Good For Two Adults & Two Children<br/>*Pay Just The Taxes & Fees<br/>*Multiple Travel Date Requests Allowed<br/>*Fully Transferable To Another Person<br/>*Just A 30 Days Advance Notice Required<br/>*You Will Have 12 Months To Complete Travel After Redemption<br/><br/>HOW CAN WE DO THIS?<br/><br/>We contract with the world leading hotel chains and resorts to help them fill their otherwise empty rooms.<br/><br/>We help fill empty rooms which the hotels, resorts and cruise lines turn into additional revenue from other areas of their property and future bookings.<br/><br/>Hotels rarely experience full occupancy, yet they remain open, providing rooms and services at fixed costs. So when hotels give out their rooms by partnering with marketing companies like us, they might miss out on the room fee, but they already didn't have that in the first place, at least now they have the opportunity to gain a customer for their in-house restaurants, room service, their casinos, an extra day stay, future bookings, etc.<br/><br/>VIEW ALL THE DETAILS OF THIS SPECIAL OFFER AND REDEEM ONLINE AT <br/>WWW.QOTAVERNIX.COM<br/><br/>Certificate ID # 47261-38157<br/>Expires 02/29/2020<br/><br/><br/>*terms and conditions apply see website for details<br/><br/>KEEP IN MIND THE EXAMPLES I AM UPLOADING ARE SIMPLY TO SHOW YOU THAT THEY CONTAIN THE "COMPLIMENTS OF" AND "EXCLUSIVELY FOR" ELEMENTS. THESE MUST BE INCLUDED IN NEW DESIGN. PLEASE ONLY USE THE CONTENT I PROVIDED IN BRIEF, DONT USE CONTENT FROM EXAMPLES.

Target Market(s)

CONSUMERS THAT HAVE BEEN REWARDED WITH A VACATION CERTIFICATE FOR DOING BUSINESS WITH A COMPANY.

COMPANIES USE THESE AS MARKETING INCENTIVES TO ATTRACT MORE CUSTOMERS AND TO REWARD LOYALTY, ETC.

Industry/Entity Type

Travel Industry

Colors

Designer to choose colors to be used in the design.

Requirements
Must have
• I need to create a beautiful flyer 8.5 x 11 PDF format flyer design.
• Instructions:
• The flyer will really be a gift voucher for a las vegas vacation getaway. So must have a Las Vegas Theme exciting fun
• The voucher should have two modules that will be editable.
• Must have a "Compliments Of" area and also must have an "Exclusively For" area
• Keep in mind that this flyer will be printed so keep that in mind :)
• Here the is the content for the vacation voucher:
• There is no doubt that Las Vegas is one of the hottest travel destinations around the world. In fact, some people would even go as far as
• saying that perhaps it is THE hottest place to visit. Enjoy up to 4 nights of resort/casino accommodations in exciting Las Vegas, NV. Millions of people travel to this exciting city each year to enjoy its thrills. Thanks to the business you received this certificate from, now you can enjoy exciting Las Vegas, NV too!
• Features:
• *Travel 7 Days A Week
• *Stay Your Choice Of Nights (1-4 Nights)
• *Good For Two Adults & Two Children
• *Pay Just The Taxes & Fees
• *Multiple Travel Date Requests Allowed
• *Fully Transferable To Another Person
• *Just A 30 Days Advance Notice Required
• *You Will Have 12 Months To Complete Travel After Redemption
• HOW CAN WE DO THIS?
• We contract with the world leading hotel chains and resorts to help them fill their otherwise empty rooms.
• We help fill empty rooms which the hotels, resorts and cruise lines turn into additional revenue from other areas of their property and future bookings.
• Hotels rarely experience full occupancy, yet they remain open, providing rooms and services at fixed costs. So when hotels give out their rooms by partnering with marketing companies like us, they might miss out on the room fee, but they already didn't have that in the first place, at least now they have the opportunity to gain a customer for their in-house restaurants, room service, their casinos, an extra day stay, future bookings, etc.
• VIEW ALL THE DETAILS OF THIS SPECIAL OFFER AND REDEEM ONLINE AT
• WWW.QOTAVERNIX.COM
• Certificate ID # 47261-38157
• Expires 02/29/2020
• *terms and conditions apply see website for details
• KEEP IN MIND THE EXAMPLES I AM UPLOADING ARE SIMPLY TO SHOW YOU THAT THEY CONTAIN THE "COMPLIMENTS OF" AND "EXCLUSIVELY FOR" ELEMENTS. THESE MUST BE INCLUDED IN NEW DESIGN. PLEASE ONLY USE THE CONTENT I PROVIDED IN BRIEF, DONT USE CONTENT FROM EXAMPLES.
Nice to have
• EXCITING LAS VEGAS IMAGES THAT MAKE SOMEONE WANT TO GO THERE

```html
<!DOCTYPE html>
<html lang="en">
<head>
<meta charset="utf-8">
<title>Las Vegas Vacation Certificate</title>
<link href="https://fonts.googleapis.com/css2?family=Bebas+Neue&family=Roboto:ital,wght@0,400;0,500;0,700;0,900;1,500&family=Roboto+Condensed:wght@700;800&display=swap" rel="stylesheet">
<style>
  :root {
    --ink: #0f0e1a;
    --text: #1c1c1c;
    --red: #e32a2c;
    --white: #ffffff;
    --gold: #8a6a3a;
    --gold-light: #c9b07a;
  }
  * { margin: 0; padding: 0; box-sizing: border-box; }
  html, body { width: 927px; height: 1200px; overflow: hidden; background: var(--white); }
  .certificate { position: relative; width: 927px; height: 1200px; font-family: "Roboto", sans-serif; color: var(--text); overflow: hidden; }

  .hero { position: absolute; left: 0; top: 0; width: 927px; height: 350px;
    background:
      radial-gradient(ellipse 60% 30% at 70% 88%, rgba(255,196,90,0.75) 0%, rgba(255,150,60,0) 70%),
      radial-gradient(ellipse 45% 40% at 20% 62%, rgba(236,90,190,0.55) 0%, rgba(236,90,190,0) 70%),
      linear-gradient(180deg, #1d4688 0%, #3f75b8 22%, #5b6e9a 38%, #3a3050 52%, #7a4a3c 68%, #e0a04a 80%, #2b2a44 92%, #1b4a70 100%); }
  .compliments { position: absolute; left: 645px; top: 51px; width: 231px; height: 232px; background: var(--white);
    text-align: center; font-weight: 700; color: #111; }
  .compliments-title { margin-top: 24px; font-size: 18.5px; line-height: 20px; letter-spacing: 0.2px; }
  .compliments-lines { position: absolute; left: 0; right: 0; top: 155px; font-size: 17.5px; line-height: 20px; font-weight: 500; }

  .exclusive-tab { position: absolute; left: 0; top: 316px; width: 357px; height: 34px; background: var(--red);
    color: var(--white); font-family: "Roboto Condensed", sans-serif; font-weight: 700; font-size: 19.8px;
    line-height: 34px; padding-left: 36px; letter-spacing: 0.2px; white-space: nowrap; }

  .title-band { position: absolute; left: 0; top: 350px; width: 927px; height: 86px; background: var(--ink);
    color: var(--white); text-align: center; font-weight: 700; font-size: 39.5px; line-height: 36px; padding-top: 8px; letter-spacing: 0.4px; white-space: nowrap; }

  .intro { position: absolute; left: 60px; width: 807px; top: 456px; text-align: center; }
  .intro-headline { font-weight: 900; font-size: 27px; line-height: 28px; letter-spacing: -1.6px; color: #111; }
  .intro-body { margin-top: 10px; font-size: 17px; line-height: 21.2px; letter-spacing: -0.55px; color: #222; white-space: nowrap; }

  .gallery-photo { position: absolute; top: 624px; width: 227px; height: 174px; border: 4px solid var(--gold-light);
    box-shadow: 0 7px 6px -4px rgba(0,0,0,0.45); }
  .photo-sign { left: 108px; background:
      radial-gradient(ellipse 45% 28% at 56% 42%, #f2e6d8 0%, #e04a6a 45%, rgba(120,40,110,0) 100%),
      radial-gradient(ellipse 70% 30% at 50% 95%, rgba(230,140,70,0.6) 0%, rgba(0,0,0,0) 100%),
      linear-gradient(180deg, #07070f 0%, #141226 60%, #2a2030 100%); }
  .photo-hotel { left: 350px; background:
      radial-gradient(ellipse 35% 25% at 35% 72%, #ff9a5a 0%, #e0503a 45%, rgba(200,60,60,0) 100%),
      linear-gradient(180deg, #0c0f1e 0%, #20263a 15%, #d8dbe2 38%, #b8bcc8 58%, #7a3a30 85%, #1a1016 100%); }
  .photo-strip { left: 592px; background:
      radial-gradient(ellipse 40% 35% at 55% 88%, #ff4a3a 0%, rgba(255,120,60,0.6) 45%, rgba(0,0,0,0) 100%),
      radial-gradient(ellipse 25% 40% at 82% 55%, rgba(240,70,160,0.7) 0%, rgba(0,0,0,0) 100%),
      radial-gradient(ellipse 20% 35% at 15% 70%, rgba(60,160,90,0.6) 0%, rgba(0,0,0,0) 100%),
      linear-gradient(180deg, #0d0f1c 0%, #1a1a2c 40%, #3a2020 100%); }

  .features { position: absolute; left: 71px; top: 830px; width: 385px; }
  .section-heading { font-family: "Bebas Neue", sans-serif; font-size: 37px; line-height: 36px; color: #111; }
  .feature-list { list-style: none; margin-top: 6px; }
  .feature-list li { position: relative; padding-left: 21px; font-size: 12.8px; line-height: 21.2px; color: #222; white-space: nowrap; }
  .feature-list li::before { content: ""; position: absolute; left: 2px; top: 5px; width: 10px; height: 10px;
    border: 1.5px solid var(--gold); background: var(--white); box-shadow: inset 0 0 0 1.5px var(--white); }
  .feature-list li::after { content: ""; position: absolute; left: 5px; top: 8px; width: 4px; height: 4px; background: var(--gold); }

  .divider { position: absolute; left: 463px; top: 817px; width: 1.5px; height: 233px; background: #111; }

  .method { position: absolute; left: 482px; top: 830px; width: 372px; }
  .method-list { list-style: none; margin-top: 7px; }
  .method-list li { position: relative; padding-left: 27px; font-size: 12.3px; line-height: 13.6px; color: #222; margin-bottom: 9px; letter-spacing: -0.2px; }
  .method-list svg { position: absolute; left: 0; top: 1px; }

  .cta { position: absolute; left: 40px; width: 847px; top: 1062px; text-align: center; font-style: italic; font-weight: 500; font-size: 26px; line-height: 27px; color: #111; }

  .footer-band { position: absolute; left: 0; top: 1136px; width: 927px; height: 64px; background: var(--ink); }
  .footer-tag { position: absolute; left: 0; top: 1113px; }
  .certificate-id { position: absolute; left: 600px; width: 300px; top: 1124px; text-align: center; color: var(--white);
    font-family: "Roboto Condensed", sans-serif; font-weight: 700; font-size: 16.4px; line-height: 17px; }
  .certificate-id small { display: block; font-size: 12.4px; line-height: 15px; letter-spacing: -0.3px; }
</style>
</head>
<body>
<main class="certificate">
  <div class="hero" role="img" aria-label="Las Vegas Strip skyline at dusk with illuminated resort casinos and fountains"></div>

  <section class="compliments">
    <p class="compliments-title">THIS CERTIFICATE IS<br>COMPLIMENTS OF</p>
    <p class="compliments-lines">Certificate Courtesy Of<br>Text Line 2<br>Text Line 3</p>
  </section>

  <div class="exclusive-tab">EXCLUSIVELY FOR : CUSTOMER NAME</div>

  <h1 class="title-band">4 Nights Of Resort Casino Accommodations<br>In Las Vegas, NV!</h1>

  <section class="intro">
    <h2 class="intro-headline">There is no doubt that Las Vegas is one of the hottest<br>travel destinations around the world.</h2>
    <p class="intro-body">In fact, some people would even go as far as saying that perhaps it is THE hottest place to visit. Enjoy up to<br>4 nights of resort/casino accommodations in exciting Las Vegas, NV. Millions of people travel to this<br>exciting city each year to enjoy its thrills. Thanks to the business you received this certificate from, now you<br>can enjoy exciting Las Vegas, NV too!</p>
  </section>

  <div class="gallery-photo photo-sign" role="img" aria-label="Welcome to Las Vegas sign lit at night between palm trees"></div>
  <div class="gallery-photo photo-hotel" role="img" aria-label="Resort hotel tower with a glowing neon entrance at night"></div>
  <div class="gallery-photo photo-strip" role="img" aria-label="Busy Las Vegas boulevard at night with traffic and neon lights"></div>

  <section class="features">
    <h3 class="section-heading">FEATURES:</h3>
    <ul class="feature-list">
      <li>Travel 7 Days A Week</li>
      <li>Stay Your Choice Of Nights (1-4 Nights)</li>
      <li>Good For Two Adults &amp; Two Children</li>
      <li>Pay Just The Taxes &amp; Fees</li>
      <li>Multiple Travel Date Requests Allowed</li>
      <li>Fully Transferable To Another Person</li>
      <li>Just A 30 Days Advance Notice Required</li>
      <li>You Will Have 12 Months To Complete Travel After Redemption</li>
    </ul>
  </section>

  <div class="divider"></div>

  <section class="method">
    <h3 class="section-heading">HOW CAN WE DO THIS?</h3>
    <ul class="method-list">
      <li><svg width="22" height="18" viewBox="0 0 22 18"><path d="M2 6h9l-1-4M2 6v9h11M11 6h10M13 9h6M13 12h5M13 15h3" fill="none" stroke="#8a6a3a" stroke-width="1.4" stroke-linecap="round"/></svg>We contract with the world leading hotel chains and resorts to help them fill their otherwise empty rooms.</li>
      <li><svg width="22" height="18" viewBox="0 0 22 18"><path d="M2 6h9l-1-4M2 6v9h11M11 6h10M13 9h6M13 12h5M13 15h3" fill="none" stroke="#8a6a3a" stroke-width="1.4" stroke-linecap="round"/></svg>We help fill empty rooms which the hotels, resorts and cruise lines turn into additional revenue from other areas of their property and future bookings.</li>
      <li><svg width="22" height="18" viewBox="0 0 22 18"><path d="M2 6h9l-1-4M2 6v9h11M11 6h10M13 9h6M13 12h5M13 15h3" fill="none" stroke="#8a6a3a" stroke-width="1.4" stroke-linecap="round"/></svg>Hotels rarely experience full occupancy, yet they remain open, providing rooms and services at fixed costs. So when hotels give out their rooms by partnering with marketing companies like us, they might miss out on the room fee, but they already didn't have that in the first place, at least now they have the opportunity to gain a customer for their in-house restaurants, room service, their casinos, an extra day stay, future bookings, etc.</li>
    </ul>
  </section>

  <p class="cta">View all the details of this special offer and Redeem online at<br>www.Qotavernix.com</p>

  <div class="footer-band"></div>
  <svg class="footer-tag" width="927" height="87" viewBox="0 0 927 87"><polygon points="632,0 927,0 927,87 557,87" fill="#e32a2c"/></svg>
  <p class="certificate-id">CERTIFICATE ID # 47261-38157<br>EXPIRES 02/29/2020<small>(Terms and conditions apply see website for details)</small></p>
</main>
</body>
</html>
```